Working Capital graphics

Our business advisory firm requires 9 images to be re-created and improved in the branding of our business.

The 9 images have been uploaded below and the colours and branding of the business can be found at the website www.tallowmereadvisory.com.au

```html
<!DOCTYPE html>
<html lang="en">
<head>
<meta charset="utf-8">
<title>Working Capital Cycles</title>
<link rel="stylesheet" href="https://fonts.googleapis.com/css2?family=Arimo:wght@400&family=PT+Serif:wght@700&display=swap">
<style>
  :root {
    --ink: #1a1a1a;
    --maroon: #7d1a20;
    --orange: #f7941d;
    --signal-red: #e52630;
    --paper: #ffffff;
  }
  html, body {
    margin: 0;
    padding: 0;
    overflow: hidden;
    background: var(--paper);
  }
  .canvas {
    position: relative;
    width: 1200px;
    height: 1000px;
    overflow: hidden;
    background: var(--paper);
    font-family: "Arimo", Arial, sans-serif;
    color: var(--ink);
  }
  .connectors {
    position: absolute;
    inset: 0;
  }
  .step {
    position: absolute;
    transform: translate(-50%, -50%);
    text-align: center;
    font-size: 20px;
    line-height: 24px;
    white-space: nowrap;
  }
  .cycle-title {
    position: absolute;
    transform: translate(-50%, -50%);
    text-align: center;
    font-family: "PT Serif", Georgia, serif;
    font-weight: 700;
    font-size: 24px;
    line-height: 29px;
    color: var(--orange);
    white-space: nowrap;
  }
  .cycle-tag {
    position: absolute;
    height: 33px;
    background: var(--maroon);
    color: var(--paper);
    font-size: 20px;
    line-height: 33px;
    text-align: center;
    white-space: nowrap;
  }
  .hub-label {
    font-family: "Arimo", Arial, sans-serif;
    font-size: 19px;
    fill: var(--paper);
  }
</style>
</head>
<body>
<div class="canvas">

  <svg class="connectors" width="1200" height="1000" viewBox="0 0 1200 1000" aria-hidden="true">
    <defs>
      <marker id="head-maroon" viewBox="0 0 10 10" refX="5" refY="5" markerWidth="3.2" markerHeight="3.2" orient="auto">
        <path d="M0 0 L10 5 L0 10 Z" fill="var(--maroon)"/>
      </marker>
      <marker id="head-red" viewBox="0 0 10 10" refX="5" refY="5" markerWidth="3.4" markerHeight="3.4" orient="auto">
        <path d="M0 0 L10 5 L0 10 Z" fill="var(--signal-red)"/>
      </marker>
    </defs>

    <g class="flow-revenue" stroke="var(--maroon)" stroke-width="3.5" marker-end="url(#head-maroon)">
      <line x1="245" y1="93" x2="263" y2="84"/>
      <line x1="366" y1="83" x2="385" y2="90"/>
      <line x1="422" y1="112" x2="435" y2="126"/>
      <line x1="467" y1="176" x2="473" y2="195"/>
      <line x1="481" y1="237" x2="481" y2="256"/>
      <line x1="460" y1="316" x2="448" y2="332"/>
      <line x1="406" y1="376" x2="389" y2="385"/>
      <line x1="268" y1="394" x2="250" y2="385"/>
      <line x1="212" y1="361" x2="197" y2="349"/>
      <line x1="166" y1="299" x2="161" y2="282"/>
      <line x1="155" y1="240" x2="155" y2="221"/>
      <line x1="185" y1="141" x2="197" y2="125"/>
    </g>

    <g class="flow-supply" stroke="var(--maroon)" stroke-width="3.5" marker-end="url(#head-maroon)">
      <line x1="800" y1="93" x2="818" y2="84"/>
      <line x1="913" y1="82" x2="932" y2="89"/>
      <line x1="998" y1="140" x2="1007" y2="157"/>
      <line x1="1027" y1="193" x2="1030" y2="212"/>
      <line x1="1025" y1="270" x2="1019" y2="287"/>
      <line x1="976" y1="351" x2="959" y2="363"/>
      <line x1="800" y1="376" x2="784" y2="367"/>
      <line x1="716" y1="290" x2="716" y2="270"/>
      <line x1="713" y1="217" x2="713" y2="199"/>
      <line x1="736" y1="153" x2="743" y2="139"/>
    </g>

    <g class="hub">
      <polygon points="470,499 773,499 622,347" fill="var(--orange)"/>
      <g stroke="var(--paper)" stroke-width="2">
        <line x1="622" y1="437" x2="470" y2="499"/>
        <line x1="622" y1="437" x2="773" y2="499"/>
        <line x1="622" y1="437" x2="622" y2="347"/>
      </g>
      <text class="hub-label" x="574" y="426" text-anchor="middle" transform="rotate(-62 574 420)">A/R</text>
      <text class="hub-label" x="666" y="420" text-anchor="middle" transform="rotate(56 666 414)">Inventory</text>
      <text class="hub-label" x="622" y="478" text-anchor="middle">A/P</text>
    </g>

    <g class="hub-pointers" stroke="var(--signal-red)" stroke-width="3" marker-end="url(#head-red)">
      <line x1="540" y1="406" x2="523" y2="388"/>
      <line x1="703" y1="406" x2="719" y2="389"/>
      <line x1="622" y1="515" x2="622" y2="546"/>
    </g>
  </svg>

  <!-- Revenue management cycle -->
  <div class="cycle-title" style="left:307px; top:229px">Revenue<br>Management</div>
  <div class="step" style="left:318px; top:70px">Customer<br>Strategy</div>
  <div class="step" style="left:455px; top:84px">Sales<br>Management</div>
  <div class="step" style="left:480px; top:140px">Risk<br>Management</div>
  <div class="step" style="left:523px; top:207px">Contract<br>Management</div>
  <div class="step" style="left:514px; top:288px">Sales Order<br>Processing</div>
  <div class="step" style="left:443px; top:371px">Credit<br>Check</div>
  <div class="step" style="left:333px; top:392px">Order<br>Fulfilment</div>
  <div class="step" style="left:211px; top:380px">Billing</div>
  <div class="step" style="left:148px; top:331px">Customer<br>Service</div>
  <div class="step" style="left:120px; top:247px">Cash<br>Collection</div>
  <div class="step" style="left:134px; top:174px">Receipt &amp;<br>Allocation<br>of Cash</div>
  <div class="step" style="left:184px; top:96px">Cash<br>Management</div>
  <div class="cycle-tag" style="left:221px; top:424px; width:190px">Customer to Cash</div>

  <!-- Supply chain management cycle -->
  <div class="cycle-title" style="left:882px; top:229px">Supply Chain<br>Management</div>
  <div class="step" style="left:875px; top:78px">Supply<br>Chain<br>Strategy</div>
  <div class="step" style="left:1016px; top:116px">Product Range<br>Management</div>
  <div class="step" style="left:1066px; top:180px">Forecasting</div>
  <div class="step" style="left:1069px; top:244px">Sales Order<br>Forecasting</div>
  <div class="step" style="left:1027px; top:327px">Production<br>Scheduling</div>
  <div class="step" style="left:881px; top:379px">Raw Material<br>Planning</div>
  <div class="step" style="left:744px; top:327px">Production<br>Planning</div>
  <div class="step" style="left:677px; top:243px">Production</div>
  <div class="step" style="left:688px; top:180px">Warehousing</div>
  <div class="step" style="left:755px; top:115px">Distribution</div>
  <div class="cycle-tag" style="left:766px; top:424px; width:232px">Forecast to Fulfilment</div>

  <!-- Expenditure management cycle -->
  <div class="cycle-title" style="left:613px; top:727px">Expenditure<br>Management</div>
  <div class="step" style="left:611px; top:591px">Purchasing<br>Strategy</div>
  <div class="step" style="left:758px; top:629px">Budgeting &amp;<br>Forecasting</div>
  <div class="step" style="left:821px; top:695px">Originating<br>Requirements</div>
  <div class="step" style="left:810px; top:772px">Selecting &amp;<br>Negotiating</div>
  <div class="step" style="left:764px; top:842px">Ordering &amp;<br>Contracting</div>
  <div class="step" style="left:620px; top:879px">Receiving &amp;<br>Evaluating</div>
  <div class="step" style="left:485px; top:842px">Discrepancy<br>Management</div>
  <div class="step" style="left:427px; top:770px">Invoice<br>Processing</div>
  <div class="step" style="left:419px; top:695px">Payment<br>Issuance</div>
  <div class="step" style="left:485px; top:620px">Cash<br>Management</div>
  <div class="cycle-tag" style="left:497px; top:924px; width:230px">Purchase to Pay</div>

</div>
</body>
</html>
```